Brenvik Systems PowerPoint Template

Project Title: Professional & Functional PowerPoint Template (.potx) – Brenvik Systems Rebrand

Project Overview:
Brenvik Systems has recently undergone a complete rebranding, including a new logo, website, and visual identity. We need a professional, high-end PowerPoint Template (.potx) that reflects our new look while being highly functional for everyday use.

We previously had a design created, but it was built incorrectly (static images, oversized file, no Master Slides). The goal of this project is to take our new aesthetic and build a "workable" template where layouts are controlled by Master Slides and text is easily editable.

Style & Brand Direction:
The template must be an extension of our new website: https://www.brenvik-systems.example/

Aesthetic: Modern, clean, high-tech, and "Industrial Tech."

Color Palette: Please pull the primary blues, greys, and accent colors directly from the website.

Imagery/Graphics: Use clean lines and subtle tech-inspired gradients. Avoid "clutter."

Tone: Innovative, precise, and professional.

Technical Requirements (Crucial)
Format: Must be delivered as a PowerPoint Template file (** .potx **).

Functionality: All layouts must be built using Slide Masters. Users should be able to click "New Slide" and choose from specific layouts.

Native Elements: Do NOT use full-page background images for text areas. Bullet points must use native PowerPoint list functionality (not individual text boxes).

File Size: The template must be optimized and lightweight.

Fonts: Use standard professional fonts or provide the specific web-safe equivalent used on our site (e.g., Montserrat, Open Sans, etc.).

Required Slide Layouts
Please include a minimum of 10–12 Master layouts, including:
*Title Slide (2-3 variations: Dark and Light)
*Agenda/Table of Contents
*Section Header/Divider Slides
*Standard Text/Bullet Slide
*Two-Column Text Slide
*Image + Text Layouts (Left/Right variations)
*Data/Chart Slide (Styled bar/pie charts that match the brand)
*Process/Timeline Slide (Infographic style)
*Section slide

Attachments Provided
Brand Assets (.zip): Contains our new logo in various formats.

Inspiration/Existing PPT: We have attached the previous design created by our web agency. Note: Use this for visual inspiration ONLY. Do not copy the file structure, as it is technically flawed.

Deliverables
Final .potx file.

All used icons or custom graphics in vector format (if applicable).

Instruction note on any specific fonts used.

Target Market(s)

Internal communication and external (investors, customers)

Industry/Entity Type

Semiconductor, Automotive

Requirements
Must have
• A potx file

```html
<!DOCTYPE html>
<html lang="en">
<head>
<meta charset="utf-8">
<title>Brenvik Systems – Presentation Template Layouts</title>
<link href="https://fonts.googleapis.com/css2?family=Poppins:wght@400;500;600;700&display=swap" rel="stylesheet">
<style>
:root{
  --brand-blue:#1428e0;
  --ink:#111114;
  --white:#ffffff;
  --mist:#e8e7ea;
  --page-top:#b3bdfb;
  --page-bottom:#e6e6ea;
  --tile:#ececf2;
  --body:#2a2a33;
}
*{margin:0;padding:0;box-sizing:border-box}
html,body{width:837px;height:1200px;overflow:hidden}
body{font-family:'Poppins',sans-serif;background:linear-gradient(180deg,var(--page-top) 0%,#c9cdf5 55%,var(--page-bottom) 100%)}
.stage{position:absolute;left:0;top:0;width:1601px;height:2296px;transform:scale(0.5228);transform-origin:0 0}
.slide{position:absolute;width:655px;height:369px;overflow:hidden;background:linear-gradient(180deg,#fff 0%,#f4f5fd 55%,#d5daf9 100%)}
.abs{position:absolute}
.brand{position:absolute;left:50px;top:46px;display:flex;align-items:center;gap:8px;font-weight:700;font-size:34px;letter-spacing:.5px;line-height:1}
.brand .mark{width:26px;height:26px}
.cover-title{position:absolute;left:50px;top:124px;font-weight:700;font-size:19.5px;line-height:25.5px;text-transform:uppercase}
.cover-sub{position:absolute;left:50px;top:256px;font-size:8.5px;line-height:15px;width:260px}
.cover-panel{position:absolute;left:379px;top:72px;width:224px;height:224px}
.cover-url{position:absolute;left:41px;top:348px;width:573px;height:21px;font-size:8px;text-align:center;line-height:21px}
.footer{position:absolute;left:41px;top:347px;width:573px;height:21px;background:var(--ink);color:var(--white);font-size:8px;line-height:21px;padding:0 17px;display:flex;justify-content:space-between}
.footer .copy{font-size:6.5px;padding-right:28px}
.header{position:absolute;left:45px;top:22px;width:355px;height:50px}
.header-title{position:absolute;left:61px;top:36px;color:var(--white);font-weight:700;font-size:15.5px;letter-spacing:.2px;line-height:30px;text-transform:uppercase;white-space:nowrap}
.lead{color:var(--brand-blue);font-size:8.3px;line-height:13.5px}
.copy-text{color:var(--body);font-size:6.6px;line-height:13.3px}
.photo{position:absolute;border-radius:50%}
.bullets{list-style:none}
.bullets li{display:flex;align-items:center;gap:5px;font-size:6.6px;color:var(--body);height:16px}
.bullets li svg{width:7px;height:7px;flex:none}
.toc-title{position:absolute;left:373px;top:46px;font-weight:600;font-size:16px;color:var(--ink)}
.toc-list{position:absolute;left:373px;top:140px;list-style:none}
.toc-list li{position:relative;padding-left:23px;font-weight:500;font-size:15px;height:38.5px;line-height:28px;color:var(--ink)}
.toc-list li.accent{color:var(--brand-blue)}
.toc-list li::before{content:"";position:absolute;left:1px;top:9px;width:11px;height:11px;border-radius:50%;background:currentColor}
.toc-line{position:absolute;left:379px;top:156px;width:2px;height:154px;background:var(--ink)}
.stat{position:absolute;top:266px}
.stat .num{color:var(--brand-blue);font-size:20px;font-weight:500;line-height:28px}
.stat .label{font-size:6.5px;color:var(--body);margin-top:6px}
.step{position:absolute;display:flex;align-items:center;gap:7px}
.step .icon{width:42px;height:42px;border-radius:50%;flex:none;display:flex;align-items:center;justify-content:center}
.step .icon.blue{background:var(--brand-blue)}
.step .icon.dark{background:var(--ink)}
.step h4{font-size:8px;font-weight:600;color:var(--ink);margin-bottom:4px}
.step p{font-size:5.6px;color:var(--body);white-space:nowrap}
.divider-title{position:absolute;left:0;width:655px;top:188px;text-align:center;color:var(--white);font-weight:700;font-size:40px;text-transform:uppercase}
.tile{position:absolute;width:108px;height:52px;background:var(--tile);display:flex;align-items:center;justify-content:center}
.tile span{display:block;background:#9a9aa6;opacity:.75}
</style>
</head>
<body>
<div class="stage">

  <!-- Title slide, dark -->
  <section class="slide" style="left:128px;top:104px;background:var(--ink)">
    <div class="abs" style="left:0;top:0;width:655px;height:239px;background:linear-gradient(120deg,#1a2de6,#1428e0 60%,#2236d8)"></div>
    <div class="brand" style="color:var(--white)"><span class="mark" style="background:var(--white)"></span>BRENVIK</div>
    <h1 class="cover-title" style="color:var(--white)">Advanced Laser<br>Manufacturing for<br>Next-Generation<br>Materials</h1>
    <p class="cover-sub" style="color:#e6e6ee">Transforming semiconductor manufacturing with precision laser technology.</p>
    <div class="cover-panel" style="background:var(--white)"></div>
    <div class="cover-url" style="background:var(--white);color:var(--ink)">www.brenvik-systems.example</div>
  </section>

  <!-- Title slide, light -->
  <section class="slide" style="left:818px;top:104px;background:var(--mist)">
    <div class="abs" style="left:0;top:0;width:655px;height:239px;background:linear-gradient(120deg,#d9dbe8,#e3e4ee 60%,#d4d6e4)"></div>
    <div class="brand" style="color:var(--brand-blue)"><span class="mark" style="background:var(--brand-blue)"></span>BRENVIK</div>
    <h1 class="cover-title" style="color:var(--ink)">Advanced Laser<br>Manufacturing for<br>Next-Generation<br>Materials</h1>
    <p class="cover-sub" style="color:var(--body)">Transforming semiconductor manufacturing with precision laser technology.</p>
    <div class="cover-panel" style="background:var(--brand-blue)"></div>
    <div class="cover-url" style="background:var(--ink);color:var(--white)">www.brenvik-systems.example</div>
  </section>

  <!-- Table of contents -->
  <section class="slide" style="left:128px;top:534px">
    <div class="abs" style="left:0;top:0;width:329px;height:369px;background:linear-gradient(160deg,#1a2ce0,#1428e0 50%,#0f1fb8)"></div>
    <div class="photo" role="img" aria-label="Photo of a laser head cutting a circuit board" style="left:70px;top:91px;width:204px;height:204px;background:radial-gradient(circle at 60% 45%,#d98ad8 0%,#7a3f9e 35%,#2a1f5e 70%,#1a1840 100%)"></div>
    <h2 class="toc-title">TABLE OF CONTENTS</h2>
    <p class="lead abs" style="left:373px;top:82px;width:245px">Lorem ipsum dolor sit amet, consectetur adipiscing elit, sed do eiusmod tempor incididunt ut labore et dolore magna aliqua. Ut enim ad minim veniamde</p>
    <div class="toc-line"></div>
    <ol class="toc-list">
      <li>ABOUT US</li>
      <li class="accent">OUR SOLUTION</li>
      <li>OUR TECHNOLOGY</li>
      <li class="accent">OUR PROCESS</li>
      <li>OUR TEAM</li>
    </ol>
  </section>

  <!-- About -->
  <section class="slide" style="left:818px;top:534px">
    <svg class="header" viewBox="0 0 355 50"><polygon points="7,3 322,3 326,8 7,8" fill="#111114"/><polygon points="4,13 343,13 322,45 4,45" fill="#1428e0"/><polygon points="336,37 347,22 348,37" fill="#111114"/></svg>
    <h2 class="header-title">About Brenvik Systems</h2>
    <p class="lead abs" style="left:50px;top:82px;width:260px">Harnessing the power of light to deliver precision, scalability, and sustainability across every stage of production.</p>
    <p class="copy-text abs" style="left:50px;top:131px;width:228px">Founded in 2014, we emerged to replace wasteful mechanical manufacturing with laser precision. Today we deliver 2.2–2.3 wafers per mm with $132M in funding. We don't optimize existing processes we eliminate them. Our breakthrough approach creates manufacturing methods that seemed impossible years ago. From California to facilities worldwide, our process reduces costs by more than 60% while cutting waste—making clean technology more accessible and efficient.</p>
    <div class="photo" role="img" aria-label="Photo of polished optical lenses standing in a row" style="left:407px;top:81px;width:191px;height:191px;background:radial-gradient(circle at 45% 45%,#6a6a70 0%,#2c2c30 45%,#111 100%)"></div>
    <div class="stat" style="left:50px"><div class="num">2014</div><div class="label">Founded in</div></div>
    <div class="stat" style="left:142px"><div class="num">2–3x</div><div class="label">improvement in wafer throughput</div></div>
    <div class="stat" style="left:297px"><div class="num">+60%</div><div class="label">cost savings at scale</div></div>
    <div class="footer"><span>www.brenvik-systems.example</span><span class="copy">Copyright©2026. All Rights Reserved</span></div>
  </section>

  <!-- Solutions -->
  <section class="slide" style="left:128px;top:964px">
    <svg class="header" viewBox="0 0 355 50"><polygon points="7,3 322,3 326,8 7,8" fill="#111114"/><polygon points="4,13 343,13 322,45 4,45" fill="#1428e0"/><polygon points="336,37 347,22 348,37" fill="#111114"/></svg>
    <h2 class="header-title">Our Solutions for SiC Wafers</h2>
    <div class="photo" role="img" aria-label="Photo of a silicon carbide wafer on a clear stand" style="left:56px;top:108px;width:192px;height:192px;background:radial-gradient(circle at 45% 45%,#f2f2f4 0%,#c9c9cf 55%,#9a9aa3 100%)"></div>
    <p class="lead abs" style="left:373px;top:113px">Product-grade precision</p>
    <p class="copy-text abs" style="left:373px;top:135px;width:232px">We deliver 2.2–2.3 wafers per mm with four quality grades aligned to your needs: MOSFET Production, Diode Production, R&amp;D, and Mechanical Grade. Our laser-cut wafers eliminate bow, warp, and subsurface damage that plague traditional manufacturing.</p>
    <ul class="bullets abs" style="left:373px;top:214px">
      <li><svg viewBox="0 0 10 10"><circle cx="5" cy="5" r="5" fill="#1428e0"/><path d="M2.6 5.2l1.6 1.5 3.2-3.3" stroke="#fff" stroke-width="1.3" fill="none"/></svg>Industry-leading yield per ingot</li>
      <li><svg viewBox="0 0 10 10"><circle cx="5" cy="5" r="5" fill="#1428e0"/><path d="M2.6 5.2l1.6 1.5 3.2-3.3" stroke="#fff" stroke-width="1.3" fill="none"/></svg>90% reduction in material waste</li>
      <li><svg viewBox="0 0 10 10"><circle cx="5" cy="5" r="5" fill="#1428e0"/><path d="M2.6 5.2l1.6 1.5 3.2-3.3" stroke="#fff" stroke-width="1.3" fill="none"/></svg>Zero bow and warp effects</li>
      <li><svg viewBox="0 0 10 10"><circle cx="5" cy="5" r="5" fill="#1428e0"/><path d="M2.6 5.2l1.6 1.5 3.2-3.3" stroke="#fff" stroke-width="1.3" fill="none"/></svg>Minimal subsurface damage</li>
    </ul>
    <div class="footer"><span>www.brenvik-systems.example</span><span class="copy">Copyright©2026. All Rights Reserved</span></div>
  </section>

  <!-- Collaboration -->
  <section class="slide" style="left:818px;top:964px">
    <svg class="header" viewBox="0 0 355 50"><polygon points="7,3 322,3 326,8 7,8" fill="#111114"/><polygon points="4,13 343,13 322,45 4,45" fill="#1428e0"/><polygon points="336,37 347,22 348,37" fill="#111114"/></svg>
    <h2 class="header-title">Collaboration Built In</h2>
    <div class="photo" role="img" aria-label="Photo of a laser nozzle above a glass wafer" style="left:60px;top:110px;width:188px;height:188px;background:radial-gradient(circle at 50% 40%,#ffffff 0%,#dcdde3 50%,#8d8f99 100%)"></div>
    <div class="step" style="left:261px;top:95px"><div class="icon blue"><svg width="20" height="20" viewBox="0 0 20 20" fill="none" stroke="#fff" stroke-width="1.3"><rect x="4" y="3" width="12" height="14" rx="1"/><path d="M7 8h6M7 11h6M7 14h4"/></svg></div><div><h4>Discovery</h4><p>Clarifying markets, stakeholders and tradeoffs to support early decisions</p></div></div>
    <div class="step" style="left:296px;top:153px"><div class="icon dark"><svg width="20" height="20" viewBox="0 0 20 20" fill="none" stroke="#fff" stroke-width="1.3"><circle cx="10" cy="10" r="7"/><circle cx="10" cy="10" r="3"/></svg></div><div><h4>Collabration</h4><p>Guiding, deploying and optimizing assets using in-house automated systems</p></div></div>
    <div class="step" style="left:295px;top:213px"><div class="icon blue"><svg width="20" height="20" viewBox="0 0 20 20" fill="none" stroke="#fff" stroke-width="1.3"><circle cx="7" cy="8" r="3"/><circle cx="13" cy="8" r="3"/><path d="M4 16h12"/></svg></div><div><h4>Delivery</h4><p>Structuring scientific truth, claims logic, and narrative consistency</p></div></div>
    <div class="step" style="left:261px;top:270px"><div class="icon dark"><svg width="20" height="20" viewBox="0 0 20 20" fill="none" stroke="#fff" stroke-width="1.3"><circle cx="10" cy="10" r="6"/><path d="M10 2v3M10 15v3M2 10h3M15 10h3"/></svg></div><div><h4>Evolution</h4><p>Translating evidence into access-ready, economically credible value</p></div></div>
    <div class="footer"><span>www.brenvik-systems.example</span><span class="copy">Copyright©2026. All Rights Reserved</span></div>
  </section>

  <!-- Divider -->
  <section class="slide" style="left:128px;top:1393px;background:var(--white)">
    <div class="abs" style="left:0;top:33px;width:655px;height:64px;background:var(--ink)"></div>
    <div class="abs" style="left:0;top:97px;width:655px;height:272px;background:var(--brand-blue)"></div>
    <h2 class="divider-title">Divider Slide</h2>
  </section>

  <!-- Technology -->
  <section class="slide" style="left:818px;top:1393px">
    <svg class="header" viewBox="0 0 355 50"><polygon points="7,3 322,3 326,8 7,8" fill="#111114"/><polygon points="4,13 343,13 322,45 4,45" fill="#1428e0"/><polygon points="336,37 347,22 348,37" fill="#111114"/></svg>
    <h2 class="header-title">Our Laser Technology</h2>
    <p class="lead abs" style="left:50px;top:106px;width:260px">Our laser technology achieves precision traditional methods can't, driving clean energy and next-generation computing.</p>
    <p class="copy-text abs" style="left:50px;top:149px;width:248px">We turn light into precision that traditional manufacturing can't achieve. Our breakthrough laser technology enables the clean energy revolution—from EV power electronics to next-generation computing.</p>
    <p class="copy-text abs" style="left:50px;top:202px;width:248px">We need brilliant minds who thrive on solving impossible problems. If you have expertise in Laser Material Processing, Optics Design, Precision Mechanical Design, or Control Systems Software Development, we want to build the future together.<br>Behind every breakthrough is a team, experience, and results that drive us forward.</p>
    <p class="lead abs" style="left:373px;top:113px">Product-grade precision</p>
    <p class="copy-text abs" style="left:373px;top:135px;width:232px">We deliver 2.2–2.3 wafers per mm with four quality grades aligned to your needs: MOSFET Production, Diode Production, R&amp;D, and Mechanical Grade. Our laser-cut wafers eliminate bow, warp, and subsurface damage that plague traditional manufacturing.</p>
    <ul class="bullets abs" style="left:373px;top:214px">
      <li><svg viewBox="0 0 10 10"><circle cx="5" cy="5" r="5" fill="#1428e0"/><path d="M2.6 5.2l1.6 1.5 3.2-3.3" stroke="#fff" stroke-width="1.3" fill="none"/></svg>Lorum Opsujm Dolor Sit Amet To</li>
      <li><svg viewBox="0 0 10 10"><circle cx="5" cy="5" r="5" fill="#1428e0"/><path d="M2.6 5.2l1.6 1.5 3.2-3.3" stroke="#fff" stroke-width="1.3" fill="none"/></svg>Lorum Opsujm Dolor Sit Amet To</li>
      <li><svg viewBox="0 0 10 10"><circle cx="5" cy="5" r="5" fill="#1428e0"/><path d="M2.6 5.2l1.6 1.5 3.2-3.3" stroke="#fff" stroke-width="1.3" fill="none"/></svg>Lorum Opsujm Dolor Sit Amet To</li>
      <li><svg viewBox="0 0 10 10"><circle cx="5" cy="5" r="5" fill="#1428e0"/><path d="M2.6 5.2l1.6 1.5 3.2-3.3" stroke="#fff" stroke-width="1.3" fill="none"/></svg>Lorum Opsujm Dolor Sit Amet To</li>
    </ul>
    <div class="footer"><span>www.brenvik-systems.example</span><span class="copy">Copyright©2026. All Rights Reserved</span></div>
  </section>

  <!-- Investors -->
  <section class="slide" style="left:510px;top:1823px">
    <svg class="header" viewBox="0 0 355 50"><polygon points="7,3 322,3 326,8 7,8" fill="#111114"/><polygon points="4,13 343,13 322,45 4,45" fill="#1428e0"/><polygon points="336,37 347,22 348,37" fill="#111114"/></svg>
    <h2 class="header-title">Our Investors</h2>
    <div class="tile" style="left:40px;top:114px"><span style="width:34px;height:10px"></span></div>
    <div class="tile" style="left:155px;top:114px"><span style="width:14px;height:14px;border-radius:50%"></span></div>
    <div class="tile" style="left:270px;top:114px"><span style="width:44px;height:6px"></span></div>
    <div class="tile" style="left:385px;top:114px"><span style="width:14px;height:14px;border-radius:50%"></span></div>
    <div class="tile" style="left:500px;top:114px"><span style="width:46px;height:6px"></span></div>
    <div class="tile" style="left:40px;top:171px"><span style="width:14px;height:14px;border-radius:50%"></span></div>
    <div class="tile" style="left:155px;top:171px"><span style="width:12px;height:14px"></span></div>
    <div class="tile" style="left:270px;top:171px"><span style="width:40px;height:10px"></span></div>
    <div class="tile" style="left:385px;top:171px"><span style="width:10px;height:10px;border-radius:50%"></span></div>
    <div class="tile" style="left:500px;top:171px"><span style="width:22px;height:24px;background:#111114;opacity:1"></span></div>
    <p class="abs" style="left:339px;top:261px;width:260px;font-size:7.8px;line-height:13.5px;color:var(--body)">Backed by world-class investors accelerating our vision for a sustainable future.</p>
    <div class="footer"><span>www.brenvik-systems.example</span><span class="copy">Copyright©2026. All Rights Reserved</span></div>
  </section>

</div>
</body>
</html>
```